eCommerce Landing Page Design for Wine Accessories using PageFly

Need to develop a landing page template that can be used for ecommerce products. This template needs to be built in PageFly (shopify App) if not in Pagefly, need an integrated app with shopify to maintain the correct url. The website is www.corklanehub.com. The template will be built using one product as an example. Copy and product images will be provided. the Landing page also must have "15% Off" and "free shipping" somewhere on the page

Although part of a website, I am open to different options on design

Target Market(s)

Wine drinkers

Requirements
Must have
• Built in PageFly (shopify App)
• Featured Product
• 15% Off
• Free Shipping
• High Converting with add to cart actions directly on the page

```html
<!DOCTYPE html>
<html lang="en">
<head>
<meta charset="utf-8">
<title>Cork Lane Hub – Wine Accessories</title>
<link href="https://fonts.googleapis.com/css2?family=Lato:wght@400;700&family=Open+Sans:wght@400;600&display=swap" rel="stylesheet">
<style>
:root{
  --red:#a50f2b;
  --ink:#222;
  --muted:#444;
  --line:#cfcfcf;
  --white:#fff;
  --card-grey:#bdbdbd;
}
*{box-sizing:border-box;margin:0;padding:0}
html,body{width:1200px;height:2885px;overflow:hidden;background:var(--white)}
body{position:relative;font-family:"Lato",sans-serif;color:var(--ink)}
.abs{position:absolute}
a{color:inherit;text-decoration:none}

/* header */
.search{left:120px;top:79px;font-size:15px;display:flex;align-items:center;gap:8px}
.brand{left:0;width:1200px;top:52px;text-align:center;font-size:40px;font-weight:700;color:var(--red);letter-spacing:1px}
.cart{left:962px;top:72px;font-size:15px;display:flex;align-items:center;gap:8px}
.nav{left:0;width:1200px;top:153px;display:flex;justify-content:center;gap:44px;font-size:17px}
.nav span.drop::after{content:"";display:inline-block;width:7px;height:7px;border-right:1.5px solid var(--ink);border-bottom:1.5px solid var(--ink);transform:rotate(45deg);margin-left:7px;position:relative;top:-4px}

/* hero */
.hero{left:0;top:202px;width:1200px;height:534px;background:linear-gradient(90deg,#8d7a6c 0%,#a3968d 25%,#9a9a9c 45%,#857e82 70%,#b9b3ad 100%)}
.hero-text{left:0;width:1200px;top:350px;text-align:center;color:var(--white)}
.hero-text .pre{font-size:31px;font-weight:700;letter-spacing:1px}
.hero-text .title{font-size:46px;font-weight:700;letter-spacing:6px;margin-top:2px}
.hero-text .sub{font-size:19px;font-weight:700;line-height:31px;margin-top:10px;letter-spacing:.5px}
.arrow{top:425px;width:52px;height:52px}
.dots{left:0;width:1200px;top:690px;display:flex;justify-content:center;gap:8px}
.dots i{width:14px;height:14px;border-radius:50%;background:var(--white);border:2px solid var(--white)}
.dots i.on{background:transparent}

/* tiles */
.tile{top:775px;width:463px;height:240px;display:flex;align-items:center;justify-content:center;color:var(--white);font-size:25px;letter-spacing:1px}
.tile.best{left:129px;background:linear-gradient(90deg,#9c8a7d,#8f4a4e 45%,#a5272f 55%,#c9bfb5)}
.tile.new{left:625px;background:linear-gradient(90deg,#b8b8b0,#8fa3b6 45%,#a2b2c2 60%,#dcd6cd)}

/* featured */
.section-title{left:0;width:1200px;text-align:center;font-size:24px;letter-spacing:.5px}
.featured-title{top:1080px;color:var(--red)}
.product{top:1135px;width:208px;text-align:center}
.product .photo{width:208px;height:242px;border:1px solid var(--line)}
.product .name{color:var(--red);font-size:18px;margin-top:22px}
.product .price{font-size:20px;font-weight:700;margin-top:8px}
.product .add{font-size:14px;margin-top:14px}
.divider{left:129px;width:959px;height:1px;background:var(--line)}

/* promo */
.promo{left:117px;top:1567px;width:966px;height:414px;background:linear-gradient(90deg,#c9a8b2,#e5c2cc 20%,#a41a45 42%,#b21f4b 58%,#ecd1d8 78%,#f2e1e4)}
.promo-text{left:117px;width:966px;top:1725px;text-align:center;color:var(--white)}
.promo-text .small{font-size:25px}
.promo-text .big{font-size:38px;margin-top:2px;letter-spacing:1px}

/* blogs */
.blogs-title{top:2050px;color:var(--ink)}
.post{top:2108px;width:304px}
.post .photo{width:304px;height:192px}
.post h3{font-family:"Open Sans",sans-serif;font-weight:400;font-size:16.5px;line-height:21px;margin-top:25px;text-transform:uppercase}
.post p{font-size:13px;line-height:20px;color:var(--muted);margin-top:10px}
.post .more{display:block;color:var(--red);font-size:13px;font-weight:700;margin-top:9px}

/* footer */
.foot-col{top:2566px}
.foot-col h4{color:var(--red);font-size:16px;font-weight:700;letter-spacing:.3px}
.foot-col ul{list-style:none;margin-top:18px}
.foot-col li{font-size:13px;height:31px}
.email{width:296px;height:34px;border:1px solid var(--line);margin-top:17px;font-size:12px;color:#888;padding:0 12px;display:flex;align-items:center;justify-content:space-between}
.social{display:flex;gap:10px;margin-top:20px}
.social i{width:20px;height:20px;border-radius:50%;background:#333}
.free p{font-size:13px;line-height:20px;color:var(--muted);margin-top:17px;width:280px}
.copy{left:106px;top:2824px;font-size:12px}
.cards{left:831px;top:2821px;display:flex;gap:12px}
.cards i{width:38px;height:24px;background:var(--card-grey);border-radius:2px}
</style>
</head>
<body>

<header>
  <div class="abs search">
    <svg width="14" height="14" viewBox="0 0 14 14"><circle cx="6" cy="6" r="4.5" fill="none" stroke="#222" stroke-width="1.5"/><line x1="9.3" y1="9.3" x2="13" y2="13" stroke="#222" stroke-width="1.5"/></svg>
    SEARCH
  </div>
  <div class="abs brand">Cork Lane Hub</div>
  <div class="abs cart">
    <svg width="26" height="26" viewBox="0 0 26 26"><path d="M8 9 V6 a5 5 0 0 1 10 0 V9" fill="none" stroke="#222" stroke-width="2"/><rect x="3" y="9" width="20" height="16" fill="#222"/><text x="13" y="21" font-size="9" fill="#fff" text-anchor="middle" font-family="Lato,sans-serif">0</text></svg>
    ITEMS
  </div>
  <nav class="abs nav">
    <span>Home</span><span>About Us</span><span class="drop">Our Products</span><span class="drop">Category</span><span>T-Shirts</span><span>House Ware</span><span>Catalog</span>
  </nav>
</header>

<section>
  <div class="abs hero" role="img" aria-label="Row of red, silver, steel and purple stemmed wine tumblers with lids"></div>
  <div class="abs hero-text">
    <div class="pre">WELCOME TO</div>
    <div class="title">CORK LANE HUB</div>
    <div class="sub">CLASS APTENT TACITI SOCIOSQU AD LITORA TORQUENT PER CONUBIA<br>NOSTRA PER INCEPTOS HYMENAEOS PROIN NULLA</div>
  </div>
  <svg class="abs arrow" style="left:47px" viewBox="0 0 52 52"><circle cx="26" cy="26" r="24" fill="none" stroke="#fff" stroke-width="2"/><path d="M29 18 L21 26 L29 34" fill="none" stroke="#fff" stroke-width="2.5"/></svg>
  <svg class="abs arrow" style="left:1111px" viewBox="0 0 52 52"><circle cx="26" cy="26" r="24" fill="none" stroke="#fff" stroke-width="2"/><path d="M23 18 L31 26 L23 34" fill="none" stroke="#fff" stroke-width="2.5"/></svg>
  <div class="abs dots"><i class="on"></i><i></i><i></i><i></i></div>
</section>

<section>
  <div class="abs tile best" role="img" aria-label="Red wine tumbler on a table">BEST SELLING</div>
  <div class="abs tile new" role="img" aria-label="Light blue wine tumbler beside a leaf">NEW ARRIVALS</div>
</section>

<section>
  <h2 class="abs section-title featured-title" style="font-weight:400">FEATURED PRODUCTS</h2>
  <div class="abs product" style="left:129px">
    <div class="photo" role="img" aria-label="Purple stemmed wine tumbler" style="background:linear-gradient(90deg,#e6ddd0,#8a3a9c 50%,#e8e0d6)"></div>
    <div class="name">PRODUCT TITLE</div><div class="price">$149.00</div><div class="add">ADD TO CART</div>
  </div>
  <div class="abs product" style="left:369px">
    <div class="photo" role="img" aria-label="Silver stemmed wine tumbler" style="background:linear-gradient(90deg,#eeeeec,#b9b9bb 50%,#ebebe8)"></div>
    <div class="name">PRODUCT TITLE</div><div class="price">$149.00</div><div class="add">ADD TO CART</div>
  </div>
  <div class="abs product" style="left:610px">
    <div class="photo" role="img" aria-label="Mint green stemmed wine tumbler" style="background:linear-gradient(90deg,#d9cfc0,#6fd3b3 50%,#ddd3c6)"></div>
    <div class="name">PRODUCT TITLE</div><div class="price">$149.00</div><div class="add">ADD TO CART</div>
  </div>
  <div class="abs product" style="left:852px">
    <div class="photo" role="img" aria-label="Lime green stemmed wine tumbler" style="background:linear-gradient(90deg,#e4ddd4,#8fae25 50%,#e8e2da)"></div>
    <div class="name">PRODUCT TITLE</div><div class="price">$149.00</div><div class="add">ADD TO CART</div>
  </div>
  <div class="abs divider" style="top:1523px"></div>
</section>

<section>
  <div class="abs promo" role="img" aria-label="Crimson wine tumbler on a pink desk beside a leaf and picture frame"></div>
  <div class="abs promo-text"><div class="small">SHOP NOW AND GET</div><div class="big">15% OFF</div></div>
  <div class="abs divider" style="top:2017px"></div>
</section>

<section>
  <h2 class="abs section-title blogs-title" style="font-weight:400">OUR BLOGS</h2>
  <article class="abs post" style="left:117px">
    <div class="photo" role="img" aria-label="Green wine tumbler on a desk" style="background:linear-gradient(90deg,#e3e4de,#43b02a 50%,#ece9e2)"></div>
    <h3>Brightwell set of 4 10cmx10cm sea navy blue ocean</h3>
    <p>nulla In ullamcorper est eget tempor cursus neque mi consectetuer mi a ultricies massa est sed nisl Class aptent taciti sociosqu ad</p>
    <a class="more" href="#">READ MORE</a>
  </article>
  <article class="abs post" style="left:448px">
    <div class="photo" role="img" aria-label="Pink wine tumbler beside a leaf" style="background:linear-gradient(90deg,#ece8e6,#c75d9c 50%,#f0ece8)"></div>
    <h3>925 sterling silver drink some wine pendants</h3>
    <p>nulla In ullamcorper est eget tempor cursus neque mi consectetuer mi a ultricies massa est sed nisl Class aptent taciti sociosqu ad</p>
    <a class="more" href="#">READ MORE</a>
  </article>
  <article class="abs post" style="left:779px">
    <div class="photo" role="img" aria-label="White wine tumbler among flowers" style="background:linear-gradient(90deg,#e8dcc6,#e6e6e4 50%,#eadfcb)"></div>
    <h3>Modern red wine fruit home decor canvas</h3>
    <p>nulla In ullamcorper est eget tempor cursus neque mi consectetuer mi a ultricies massa est sed nisl Class aptent taciti sociosqu ad</p>
    <a class="more" href="#">READ MORE</a>
  </article>
  <div class="abs divider" style="top:2511px;left:117px;width:966px"></div>
</section>

<footer>
  <div class="abs foot-col" style="left:116px">
    <h4>QUICK LINKS</h4>
    <ul><li>Home</li><li>Our Category</li><li>New Products</li><li>Special Offers</li></ul>
  </div>
  <div class="abs foot-col" style="left:296px">
    <h4>MY ACCOUNT</h4>
    <ul><li>Wishlist</li><li>Register</li><li>My Cart</li><li>My Account</li></ul>
  </div>
  <div class="abs foot-col" style="left:465px">
    <h4>NEWSLETTER</h4>
    <div class="email">your@email.com
      <svg width="18" height="12" viewBox="0 0 18 12"><rect x="0.5" y="0.5" width="17" height="11" fill="none" stroke="#aaa"/><path d="M0.5 0.5 L9 7 L17.5 0.5" fill="none" stroke="#aaa"/></svg>
    </div>
    <div class="social"><i></i><i></i><i></i><i></i><i></i></div>
  </div>
  <div class="abs foot-col free" style="left:798px">
    <h4>FREE SHIPPING</h4>
    <p>interdum vel blandit sed nulla In ullamcorper est eget tempor cursus neque mi consectetuer mi a ultricies massa est sed nisl Class</p>
  </div>
  <div class="abs divider" style="top:2794px;left:117px;width:966px"></div>
  <div class="abs copy">© 2018 Company Name &nbsp;All right reserved &nbsp;Terms of Use</div>
  <div class="abs cards"><i></i><i></i><i></i><i></i><i></i></div>
</footer>

</body>
</html>
```